Advertisement Design Project

I need an advertisement to introduce the first chemical free toilet bowl cleaner.........Brivora Lumastone,.....cartridge that you drop in your toilet tank that prevents water from staining your toilet for 5 years or 50,000 flushes......completely chemical free, safe for kids and pets, the next generation toilet bowl cleaner......technology replaces chemistry in the bathroom......saves money. safe for kids, safe for pets, safe for the environment, no poisonous chemicals........

Target Market(s)

Women 18-70

Industry/Entity Type

Environment

Requirements
Must have
• Chemical Free Toilet Bowl Cleaner
Lasts 5 Years or 50,000 flushes
Saves money on chemical cleaners
Safe for kids & pets
Safe for environment
Nice to have
• Next generation of toilet bowl cleaner
Technology replaces chemistry in the bathroom
Prolongs life of toilet tank parts

```html
<!DOCTYPE html>
<html lang="en">
<head>
<meta charset="utf-8">
<title>Brivora Lumastone – Chemical-free Toilet Bowl Cleaner</title>
<link href="https://fonts.googleapis.com/css2?family=Kalam:wght@300;400&family=Roboto:wght@400;700;900&family=Roboto+Condensed:wght@700;900&display=swap" rel="stylesheet">
<style>
  :root {
    --page: #ffffff;
    --ad-blue: #15669b;
    --glow-blue: #22aee6;
    --badge-yellow: #ffd400;
    --headline-yellow: #f8c400;
    --flush-red: #e3202b;
    --ink: #111111;
    --white: #ffffff;
  }
  * { box-sizing: border-box; margin: 0; padding: 0; }
  html, body { width: 1200px; height: 1000px; overflow: hidden; background: var(--page); }
  .advert {
    position: absolute; left: 213px; top: 10px; width: 767px; height: 980px;
    background: var(--ad-blue); overflow: hidden;
    font-family: "Roboto", Arial, sans-serif; color: var(--white);
  }
  .headline {
    position: absolute; top: 64px; left: 0; width: 100%; text-align: center;
    font-family: "Kalam", cursive; font-weight: 300; font-size: 40px; line-height: 40px; letter-spacing: 1.5px;
  }
  .headline .first {
    display: inline-block; font-family: "Roboto", Arial, sans-serif; font-weight: 700;
    font-size: 42px; color: var(--headline-yellow); border-bottom: 3px solid var(--headline-yellow);
    line-height: 42px; padding: 0 2px; margin: 0 14px; vertical-align: 6px; letter-spacing: 0;
  }
  .headline .line2 { display: block; margin-top: 0; }

  .lifespan-badge {
    position: absolute; left: 284px; top: 205px; width: 232px; height: 232px;
    border-radius: 50%; background: var(--badge-yellow);
    display: flex; flex-direction: column; align-items: center; justify-content: center;
    font-family: "Roboto Condensed", "Arial Narrow", sans-serif; color: var(--ink); text-align: center;
  }
  .lifespan-badge .lasts { font-weight: 700; font-size: 17px; line-height: 19px; }
  .lifespan-badge .years { font-weight: 900; font-size: 20px; line-height: 21px; }
  .lifespan-badge .or { font-weight: 700; font-size: 15px; line-height: 16px; }
  .lifespan-badge .count { font-weight: 900; font-size: 62px; line-height: 64px; color: var(--flush-red); letter-spacing: -1px; }
  .lifespan-badge .unit { font-weight: 900; font-size: 15px; line-height: 18px; letter-spacing: 7px; margin-left: 7px; }

  .product-glow {
    position: absolute; left: 40px; top: 420px; width: 700px; height: 320px;
    background: radial-gradient(ellipse at center, var(--glow-blue) 0%, rgba(34,174,230,0.55) 30%, rgba(21,102,155,0) 65%);
  }
  .product-photo {
    position: absolute; left: 230px; top: 470px; width: 340px; height: 200px;
    background: radial-gradient(ellipse at center, #f4f7f9 0%, rgba(230,238,243,0.85) 40%, rgba(34,174,230,0) 72%);
  }

  .benefits { position: absolute; list-style: none; font-size: 15px; letter-spacing: 0.4px; }
  .benefits li { position: relative; padding-left: 13px; }
  .benefits li::before { content: "•"; position: absolute; left: 0; }
  .benefits--left { left: 105px; top: 719px; }
  .benefits--left li { height: 26.5px; line-height: 26.5px; }
  .benefits--right { left: 473px; top: 715px; }
  .benefits--right li.two-line { line-height: 33px; height: 78px; }
  .benefits--right li.single { line-height: 32px; }

  .brand-name {
    position: absolute; top: 870px; left: 0; width: 100%; text-align: center;
    font-weight: 900; font-size: 26px; letter-spacing: 1px; color: var(--badge-yellow);
  }
  .web-address { position: absolute; top: 921px; left: 0; width: 100%; text-align: center; font-size: 15px; letter-spacing: 0.5px; }
</style>
</head>
<body>
<main class="advert">
  <h1 class="headline">The<span class="first">FIRST</span>chemical-free<span class="line2">toilet bowl cleaner</span></h1>

  <div class="lifespan-badge">
    <span class="lasts">Lasts</span>
    <span class="years">5 YEARS</span>
    <span class="or">or</span>
    <span class="count">50,000</span>
    <span class="unit">FLUSHES</span>
  </div>

  <div class="product-glow"></div>
  <div class="product-photo" role="img" aria-label="Photo of two white Brivora Lumastone tank cartridges"></div>

  <ul class="benefits benefits--left">
    <li>Save money on chemical cleaners</li>
    <li>Safe for kids &amp; pets</li>
    <li>Safe for invironment</li>
    <li>Next generation toilet bowl cleaner</li>
  </ul>
  <ul class="benefits benefits--right">
    <li class="two-line">Technology replaces chemistry<br>in the bathroom</li>
    <li class="single">Prolong life of toilet tank parts</li>
  </ul>

  <p class="brand-name">BRIVORA</p>
  <p class="web-address">www.brivoralumastone.com</p>
</main>
</body>
</html>
```